Stationery Design Project

Hi All,

We need you to design stationary for a new Business and Accounting Advisory Firm. We have already got the logo designed and it is attached. If you could also if possible, match the fonts in your design to that on the logo’s provided.

What we need:
- Business Card
- A4 Letter head
- A4 Folders
- PPT template (Title page and regular page)

And what ever else you want to throw in.

We are in the process of getting the web site designed, however below is a list of websites which we like which will give you an understanding of the style that we are going for.

- plivant.example
- moldrabay.example
- tarvenhook.example
- quillorbank.example

I look forward to your seeing your design.
Updates

Hi All,

I have just realised that I forgot that i need to include a Sworn Ledgerkeepers image on the letter head, please find attaced as File 1. Could you please have this image in the bottom left header.

Regards,

Marcus

Industry/Entity Type

Business

Requirements
Must have
• Outputs:
- Documents ready to print
- Generic editable information
- Pdf copies of the documents
- Word version of letterhead

```html
<!DOCTYPE html>
<html lang="en">
<head>
<meta charset="utf-8">
<title>Norrowby Partners – Stationery Suite</title>
<link rel="stylesheet" href="https://fonts.googleapis.com/css2?family=Open+Sans:wght@400;600;700&family=Lato:wght@400;700&display=swap">
<style>
:root{
  --stage:#a8aaad;
  --paper:#ffffff;
  --paper-shade:#f3f4f6;
  --navy:#2b4a86;
  --blue:#1f86c8;
  --blue-deep:#2a5aa6;
  --orange:#f3922a;
  --ink:#3a3a3a;
  --muted:#8a8d92;
  --rule:#b9bcc0;
  --bullet:#d8262d;
  --label:#ffffff;
}
*{box-sizing:border-box;margin:0;padding:0}
html,body{width:1200px;height:420px;overflow:hidden}
body{background:var(--stage);font-family:"Open Sans",Arial,sans-serif;color:var(--ink);position:relative}
.sheet{position:absolute;background:var(--paper);overflow:hidden}
.suite-label{position:absolute;color:var(--label);font-family:"Lato",Arial,sans-serif;font-size:13px;text-align:center}

/* brand lockup: name + plain circle */
.brand{display:flex;align-items:center;gap:4px;white-space:nowrap}
.brand-dot{border-radius:50%;background:var(--blue);flex:none}
.brand-name{font-family:"Lato",Arial,sans-serif;font-weight:400;color:var(--navy)}
.brand--sm .brand-dot{width:9px;height:9px}.brand--sm .brand-name{font-size:7.5px}
.brand--md .brand-dot{width:13px;height:13px}.brand--md .brand-name{font-size:10px}
.brand--lg .brand-dot{width:18px;height:18px}.brand--lg .brand-name{font-size:13px}
.brand--reverse .brand-dot{background:#fff}.brand--reverse .brand-name{color:#fff}

.fine{font-size:3px;line-height:1.5;color:var(--muted)}
.web{font-size:3.6px;color:var(--ink);font-weight:600;letter-spacing:.2px}
.ghost-mark{position:absolute;border-radius:50%;background:radial-gradient(circle,rgba(31,134,200,.09),rgba(243,146,42,.07));}

/* folder */
.folder-band{position:absolute;left:0;bottom:0;width:100%;height:46px;background:linear-gradient(90deg,#2a5aa6,#3b7bc6);display:flex;align-items:center;justify-content:center}
.folder-pocket{position:absolute;left:0;bottom:0;width:100%;height:46px;background:var(--paper);border-top:1px solid #dcdde0;display:flex;align-items:center;justify-content:center}

/* letterhead */
.lh-foot{position:absolute;bottom:6px;right:8px;text-align:right}
.seal{position:absolute;left:4px;bottom:4px;width:20px;height:20px;border-radius:50%;background:#b52025}
.seal-caption{position:absolute;left:26px;bottom:7px;font-size:4.6px;font-weight:700;line-height:1.05;color:#111}
.contact-top{position:absolute;top:6px;right:8px;font-size:2.8px;line-height:1.6;color:var(--muted)}

/* fax */
.fax-title{position:absolute;left:8px;top:48px;font-size:11px;color:#222}
.fax-fields{position:absolute;left:8px;top:68px;width:138px;display:grid;grid-template-columns:1fr 1fr;column-gap:14px}
.fax-fields span{font-size:2.8px;border-bottom:.6px solid var(--rule);height:8px;line-height:8px;color:var(--muted)}
.fax-checks{position:absolute;left:8px;top:118px;display:flex;gap:8px;font-size:2.8px;color:var(--muted)}
.fax-checks span::before{content:"";display:inline-block;width:3.5px;height:3.5px;border:.5px solid #777;margin-right:2px;vertical-align:middle}

/* envelope */
.env{position:absolute;background:var(--paper);box-shadow:0 0 0 .5px #d6d7da}

/* cards */
.card{position:absolute;top:200px;height:44px;background:var(--paper);padding:5px}

/* slides */
.slide{top:268px;width:161px;height:120px}
.slide-title{position:absolute;left:14px;top:7px;font-size:6.5px;font-weight:700;color:#333}
.slide-web{position:absolute;bottom:5px;left:0;width:100%;text-align:center}
.bullets{position:absolute;left:14px;top:30px;list-style:none}
.bullets li{font-size:2.9px;font-weight:600;color:#444;margin-bottom:6px;position:relative;padding-left:5px}
.bullets li::before{content:"";position:absolute;left:0;top:.7px;width:2px;height:2px;border-radius:50%;background:var(--bullet)}
.subs{position:absolute;top:28px;width:62px}
.subs div{margin-bottom:9px}
.subs b{display:block;font-size:3px;color:#333;position:relative;padding-left:4px}
.subs b::before{content:"";position:absolute;left:0;top:.8px;width:1.8px;height:1.8px;border-radius:50%;background:var(--bullet)}
.subs p{font-size:2.6px;color:var(--muted);padding-left:4px;line-height:1.4}
.photo{position:absolute;top:50px;height:58px}
</style>
</head>
<body>

<!-- FOLDER -->
<section class="sheet" style="left:19px;top:4px;width:154px;height:262px;background:linear-gradient(180deg,#f8f8f9,#eef0f2)">
  <div class="ghost-mark" style="left:22px;top:60px;width:110px;height:110px"></div>
  <div class="brand brand--md" style="position:absolute;left:18px;top:180px"><span class="brand-dot"></span><span class="brand-name">Norrowby Partners</span></div>
  <p class="fine" style="position:absolute;left:18px;top:203px">12 Harbour Lane, Carrow City, NSW 2000</p>
  <p class="fine" style="position:absolute;left:18px;top:209px">T 02 5550 1840 E hello@norrowbypartners.example</p>
  <div class="folder-band"><div class="brand brand--lg brand--reverse"><span class="brand-name">Norrowby Partners</span></div></div>
</section>
<section class="sheet" style="left:173px;top:4px;width:155px;height:262px;background:linear-gradient(180deg,#ffffff,#f3f4f6)">
  <div class="brand brand--lg" style="position:absolute;left:26px;top:68px"><span class="brand-dot"></span><span class="brand-name">Norrowby Partners</span></div>
  <p class="web" style="position:absolute;left:50px;top:212px">www.norrowbypartners.example</p>
  <div class="folder-pocket"><div class="brand brand--lg"><span class="brand-dot" style="background:var(--orange)"></span><span class="brand-name">Norrowby Partners</span></div></div>
</section>
<p class="suite-label" style="left:19px;top:266px;width:154px">Folder</p>

<!-- LETTERHEAD OPTION 1 -->
<section class="sheet" style="left:343px;top:19px;width:154px;height:217px">
  <div class="brand brand--md" style="position:absolute;left:36px;top:14px"><span class="brand-dot"></span><span class="brand-name">Norrowby Partners</span></div>
  <div class="ghost-mark" style="left:40px;top:80px;width:72px;height:72px"></div>
  <span class="seal" aria-hidden="true"></span>
  <div class="lh-foot"><p class="fine">12 Harbour Lane, Carrow City, NSW 2000</p><p class="fine">T 02 5550 1840 E hello@norrowbypartners.example</p></div>
</section>
<p class="suite-label" style="left:343px;top:236px;width:154px">Option-1</p>

<!-- LETTERHEAD OPTION 2 -->
<section class="sheet" style="left:518px;top:19px;width:153px;height:217px">
  <div class="brand brand--md" style="position:absolute;left:6px;top:8px"><span class="brand-dot"></span><span class="brand-name">Norrowby Partners</span></div>
  <div class="contact-top"><p>T 02 5550 1840</p><p>F 02 5550 1841</p><p>hello@norrowbypartners.example</p></div>
  <span class="seal" aria-hidden="true"></span>
  <p class="seal-caption">Sworn<br>Ledgerkeeper</p>
  <div class="lh-foot"><p class="fine">12 Harbour Lane, Carrow City, NSW 2000</p></div>
</section>
<p class="suite-label" style="left:518px;top:236px;width:153px">Option-2</p>

<!-- FAX OPTION 3 -->
<section class="sheet" style="left:693px;top:19px;width:154px;height:217px">
  <div class="brand brand--md" style="position:absolute;left:6px;top:8px"><span class="brand-dot"></span><span class="brand-name">Norrowby Partners</span></div>
  <div class="contact-top"><p>T 02 5550 1840</p><p>F 02 5550 1841</p><p>hello@norrowbypartners.example</p></div>
  <h2 class="fax-title">FAX</h2>
  <div class="fax-fields"><span>To</span><span>From</span><span>Fax</span><span>Pages</span><span>Phone</span><span>Date</span><span>Re</span><span>CC</span></div>
  <div class="fax-checks"><span>Urgent</span><span>For Review</span><span>Please Comment</span><span>Please Reply</span><span>Please Recycle</span></div>
  <p class="fine" style="position:absolute;bottom:5px;left:0;width:100%;text-align:center">12 Harbour Lane, Carrow City, NSW 2000</p>
</section>
<p class="suite-label" style="left:693px;top:236px;width:154px">Option-3</p>

<!-- ENVELOPES -->
<section class="env" style="left:948px;top:33px;width:177px;height:77px">
  <svg width="177" height="32" style="position:absolute;top:0;left:0" aria-hidden="true"><defs><linearGradient id="flap" x1="0" x2="1"><stop offset="0" stop-color="#2a5aa6"/><stop offset=".5" stop-color="#3d8fd3"/><stop offset="1" stop-color="#2a5aa6"/></linearGradient></defs><path d="M0 0H177V22L88 32 0 22Z" fill="url(#flap)"/></svg>
  <div class="brand brand--md brand--reverse" style="position:absolute;left:55px;top:8px"><span class="brand-name">Norrowby Partners</span></div>
</section>
<section class="env" style="left:928px;top:104px;width:177px;height:76px">
  <p class="web" style="position:absolute;left:8px;bottom:5px">www.norrowbypartners.example</p>
</section>
<section class="env" style="left:910px;top:65px;width:176px;height:80px">
  <svg width="176" height="36" style="position:absolute;top:0;left:0" aria-hidden="true"><path d="M0 0L88 34 176 0" fill="none" stroke="#c9cbce" stroke-width=".8"/></svg>
  <div class="brand brand--sm" style="position:absolute;left:66px;top:8px"><span class="brand-dot" style="background:var(--orange)"></span><span class="brand-name">Norrowby</span></div>
  <div class="brand brand--md" style="position:absolute;left:24px;top:42px"><span class="brand-dot"></span><span class="brand-name">Norrowby Partners</span></div>
  <p class="fine" style="position:absolute;left:24px;top:58px">12 Harbour Lane, Carrow City, NSW 2000</p>
</section>

<!-- BUSINESS CARDS -->
<section class="card" style="left:854px;width:85px">
  <div class="brand brand--sm"><span class="brand-dot"></span><span class="brand-name">Norrowby Partners</span></div>
  <div class="fine" style="margin-top:4px"><p>T 02 5550 1840</p><p>F 02 5550 1841</p><p>hello@norrowbypartners.example</p></div>
</section>
<section class="card" style="left:945px;width:80px">
  <div class="brand brand--sm"><span class="brand-dot"></span><span class="brand-name">Norrowby Partners</span></div>
  <div class="fine" style="margin-top:4px"><p>T 02 5550 1840</p><p>F 02 5550 1841</p><p>hello@norrowbypartners.example</p></div>
  <div class="fine" style="position:absolute;right:5px;top:18px;text-align:right"><p style="color:var(--navy)">Marcus Hale</p><p>Director</p></div>
</section>
<section class="card" style="left:1029px;width:80px;display:flex;align-items:center;justify-content:center">
  <div class="brand brand--sm"><span class="brand-dot"></span><span class="brand-name">Norrowby Partners</span></div>
</section>
<section class="card" style="left:1112px;width:81px;background:linear-gradient(135deg,#2a5aa6,#3a78c0);display:flex;align-items:center;justify-content:center">
  <div class="brand brand--md brand--reverse"><span class="brand-name">Norrowby</span></div>
</section>

<!-- PRESENTATION -->
<section class="sheet slide" style="left:166px">
  <div class="brand brand--lg" style="position:absolute;left:22px;top:30px"><span class="brand-dot"></span><span class="brand-name">Norrowby Partners</span></div>
  <p style="position:absolute;top:70px;width:100%;text-align:center;font-size:8px;font-weight:700;color:#333">TITLE OF PRESENTATION</p>
  <p class="web slide-web">www.norrowbypartners.example</p>
</section>

<section class="sheet slide" style="left:334px">
  <h3 class="slide-title" style="left:0;width:100%;text-align:center">LOREM IPSUM</h3>
  <p style="position:absolute;left:16px;top:20px;width:130px;font-size:2.7px;line-height:1.5;color:var(--muted)">Lorem ipsum dolor sit amet, consectetuer adipiscing elit, sed diam nonummy nibh euismod tincidunt ut laoreet dolore magna aliquam erat volutpat. Ut wisi enim ad minim veniam, quis nostrud exerci tation.</p>
  <div class="photo" role="img" aria-label="Photo of business partners shaking hands" style="left:8px;width:72px;background:linear-gradient(160deg,#cfd6de,#5d6672)"></div>
  <div class="photo" role="img" aria-label="Photo of hands reviewing financial documents" style="left:82px;width:72px;background:linear-gradient(160deg,#e4e6e8,#6f6a66)"></div>
</section>

<section class="sheet slide" style="left:507px">
  <h3 class="slide-title">LOREM IPSUM</h3>
  <svg width="161" height="100" viewBox="0 0 161 100" style="position:absolute;left:0;top:20px" font-family="Open Sans, sans-serif">
    <defs>
      <linearGradient id="tab" x1="0" x2="0" y1="0" y2="1"><stop offset="0" stop-color="#f7a94a"/><stop offset="1" stop-color="#e8781a"/></linearGradient>
      <linearGradient id="cyl" x1="0" x2="1"><stop offset="0" stop-color="#1d5d9c"/><stop offset=".5" stop-color="#3fa0dc"/><stop offset="1" stop-color="#1d5d9c"/></linearGradient>
    </defs>
    <g font-size="3" fill="#fff" text-anchor="middle">
      <g><rect x="20" y="5" width="26" height="7" fill="url(#tab)"/><text x="33" y="9.8">Lorem</text></g>
      <g><rect x="52" y="5" width="26" height="7" fill="url(#tab)"/><text x="65" y="9.8">Lorem</text></g>
      <g><rect x="84" y="5" width="26" height="7" fill="url(#tab)"/><text x="97" y="9.8">Lorem</text></g>
      <g><rect x="116" y="5" width="26" height="7" fill="url(#tab)"/><text x="129" y="9.8">Lorem</text></g>
    </g>
    <g id="col" font-size="2.6" fill="#fff" text-anchor="middle">
      <g><rect x="23" y="20" width="20" height="12" fill="url(#cyl)"/><ellipse cx="33" cy="32" rx="10" ry="3" fill="#1d5d9c"/><ellipse cx="33" cy="20" rx="10" ry="3" fill="#6cc0ee"/><text x="33" y="28">Lorem</text></g>
      <g><rect x="23" y="42" width="20" height="12" fill="url(#cyl)"/><ellipse cx="33" cy="54" rx="10" ry="3" fill="#1d5d9c"/><ellipse cx="33" cy="42" rx="10" ry="3" fill="#6cc0ee"/><text x="33" y="50">Lorem</text></g>
      <g><rect x="23" y="64" width="20" height="12" fill="url(#cyl)"/><ellipse cx="33" cy="76" rx="10" ry="3" fill="#1d5d9c"/><ellipse cx="33" cy="64" rx="10" ry="3" fill="#6cc0ee"/><text x="33" y="72">Lorem</text></g>
    </g>
    <use href="#col" x="32"/><use href="#col" x="64"/><use href="#col" x="96"/>
  </svg>
</section>

<section class="sheet slide" style="left:680px">
  <h3 class="slide-title">LOREM IPSUM</h3>
  <ul class="bullets">
    <li>Lorem ipsum dolor sit amet, consectetuer adipiscing elit, sed diam nonummy.</li>
    <li>Lorem ipsum dolor sit amet, consectetuer adipiscing elit, sed diam nonummy.</li>
    <li>Lorem ipsum dolor sit amet, consectetuer adipiscing elit, sed diam nonummy.</li>
    <li>Lorem ipsum dolor sit amet, consectetuer adipiscing elit, sed diam nonummy.</li>
    <li>Lorem ipsum dolor sit amet, consectetuer adipiscing elit, sed diam nonummy.</li>
    <li>Lorem ipsum dolor sit amet, consectetuer adipiscing elit.</li>
  </ul>
  <div class="ghost-mark" style="right:10px;bottom:6px;width:22px;height:22px"></div>
</section>

<section class="sheet slide" style="left:852px">
  <h3 class="slide-title">LOREM IPSUM</h3>
  <div class="subs" style="left:14px">
    <div><b>Sub Title-1</b><p>Lorem ipsum dolor sit amet, consectetuer.</p></div>
    <div><b>Sub Title-2</b><p>Lorem ipsum dolor sit amet, consectetuer.</p></div>
    <div><b>Sub Title-3</b><p>Lorem ipsum dolor sit amet, consectetuer.</p></div>
  </div>
  <div class="subs" style="left:85px">
    <div><b>Sub Title-1</b><p>Lorem ipsum dolor sit amet, consectetuer.</p></div>
    <div><b>Sub Title-2</b><p>Lorem ipsum dolor sit amet, consectetuer.</p></div>
    <div><b>Sub Title-3</b><p>Lorem ipsum dolor sit amet, consectetuer.</p></div>
  </div>
  <div class="ghost-mark" style="right:14px;bottom:6px;width:22px;height:22px"></div>
</section>

<section class="sheet slide" style="left:1020px">
  <div class="brand brand--lg" style="position:absolute;left:24px;top:28px"><span class="brand-dot"></span><span class="brand-name">Norrowby Partners</span></div>
  <p style="position:absolute;top:58px;width:100%;text-align:center;font-family:'Lato',Arial,sans-serif;font-size:11px;font-weight:700;color:var(--blue-deep)">Thank You!</p>
  <p style="position:absolute;top:74px;width:100%;text-align:center;font-size:5.5px;font-weight:700;color:#333">For your attention</p>
  <p class="web" style="position:absolute;top:84px;width:100%;text-align:center">www.norrowbypartners.example</p>
</section>

<p class="suite-label" style="left:166px;top:393px;width:846px;font-size:16px">PowerPoint Presentation</p>

</body>
</html>
```